WordPress Site That Reviews Footwear

We need a wordpress web design for an affiliate site called PaceKite. We review and do roundups on footwear products. The final design should be clean and mobile friendly. The site should be built with Gutenberg page builder. We like the design of https://lunavessel.com/.
Updates

Need extra days to review

Target Market(s)

USA

Industry/Entity Type

Footwear

Logo Text

PaceKite

Number of Pages Required

4 page

Font styles to use
Serif
Sans Serif

Requirements
Must have
• Wordpress site
Blog post
Page
Categories
Homepage

```html
<!DOCTYPE html>
<html lang="en">
<head>
<meta charset="utf-8">
<title>PaceKite – Footwear Reviews &amp; Roundups</title>
<link rel="stylesheet" href="https://fonts.googleapis.com/css2?family=Archivo:ital,wght@1,800;1,900&family=Montserrat:wght@400;500;600&display=swap">
<style>
:root{
  --red:#f40000;
  --ink:#111111;
  --panel:#454545;
  --footer:#3a3a3a;
  --white:#ffffff;
  --mist:#e9ecef;
  --muted:#d8d8d8;
}
*{box-sizing:border-box;margin:0;padding:0}
html,body{width:1200px;height:3645px;overflow:hidden}
body{position:relative;background:var(--white);font-family:"Montserrat",Arial,sans-serif;color:var(--ink)}
.abs{position:absolute}
.display{font-family:"Archivo","Arial Black",sans-serif;font-style:italic;font-weight:900;text-transform:uppercase;letter-spacing:-0.5px}

/* hero */
.hero{left:0;top:0;width:1200px;height:735px;
  background:radial-gradient(ellipse 60% 50% at 70% 45%,#8c94a3 0%,#5c6473 40%,transparent 75%),
  linear-gradient(180deg,#1b1f29 0%,#3a404c 45%,#4a4a4c 75%,#2e2e30 100%)}
.hero-photo{left:560px;top:0;width:640px;height:735px;
  background:radial-gradient(ellipse 45% 55% at 55% 55%,rgba(40,48,70,.85),rgba(40,48,70,0) 70%)}
.brand{left:173px;top:70px;color:var(--white);font-size:20px}
.brand-dot{left:173px;top:36px;width:14px;height:14px;border-radius:50%;background:var(--red)}
.nav{top:37px;right:173px;display:flex;gap:34px;color:var(--white);font-size:14px}
.hero-title{left:173px;top:215px;color:var(--white);font-size:52px;line-height:60px}
.hero-sub{left:173px;top:300px;color:var(--white);font-size:28px;line-height:42px;white-space:nowrap}
.btn{display:flex;align-items:center;justify-content:center;font-family:"Archivo",sans-serif;font-style:italic;font-weight:900;font-size:14px;text-transform:uppercase}
.btn-light{left:173px;top:416px;width:127px;height:57px;background:var(--white);color:var(--ink)}
.arrows{display:flex;gap:12px}

/* mist */
.mist{left:0;width:1200px;background:radial-gradient(ellipse 50% 40% at 20% 50%,var(--mist),transparent 70%),radial-gradient(ellipse 40% 35% at 85% 40%,var(--mist),transparent 70%)}

/* about */
.h2{font-size:32px;line-height:44px}
.red{color:var(--red)}
.about-title{left:173px;top:858px}
.body-text{font-size:12px;line-height:28px;color:#222;text-align:justify}
.about-text{left:173px;top:922px;width:392px}
.btn-red{left:173px;top:1120px;width:127px;height:57px;background:var(--red);color:var(--white)}
.about-card{left:652px;top:840px;width:375px;height:359px;background:var(--white);border-radius:16px;box-shadow:0 4px 24px rgba(0,0,0,.12)}
.about-img{left:603px;top:890px;width:394px;height:261px;background:linear-gradient(180deg,#8e969d 0%,#a8a196 55%,#7b6e5c 100%)}

.center-title{left:0;width:1200px;text-align:center}

/* review panels */
.panel{background:var(--panel);color:var(--white)}
.panel-right{left:557px;top:1457px;width:643px;height:451px;border-radius:16px 0 0 16px}
.panel-left{left:0;top:2150px;width:645px;height:451px;border-radius:0 16px 16px 0}
.photo{border-radius:14px;box-shadow:0 6px 20px rgba(0,0,0,.2)}
.review-img{left:173px;top:1533px;width:445px;height:300px;background:linear-gradient(180deg,#6f9bc4 0%,#7d8a86 40%,#8a7658 70%,#b59a6a 100%)}
.roundup-img{left:582px;top:2226px;width:445px;height:300px;background:linear-gradient(180deg,#a9b9c4 0%,#c7bda8 35%,#9c8668 70%,#6f5c46 100%)}
.item-title{font-size:20px}
.item-text{font-size:11.5px;line-height:24px;color:#eee;width:370px}

/* products */
.product{top:2856px;width:213px;height:182px;background:var(--white);border-radius:12px;box-shadow:0 4px 18px rgba(0,0,0,.1)}
.product-shoe{left:22px;top:50px;width:169px;height:80px;border-radius:40px;background:linear-gradient(180deg,#2a2a2a 0%,#1a1a1a 70%,#e8e2d6 100%)}

/* footer */
.footer{left:0;top:3168px;width:1200px;height:477px;background:var(--footer)}
.foot-brand{left:173px;top:3370px;font-size:32px;color:var(--white)}
.foot-dot{left:173px;top:3326px;width:28px;height:28px;border-radius:50%;border:3px solid var(--white)}
.foot-h{font-size:17px;line-height:28px;color:var(--white)}
.email{left:478px;top:3340px;width:253px;height:48px;background:var(--white);color:#333;font-size:11px;display:flex;align-items:center;padding-left:13px}
.subscribe{left:478px;top:3403px;width:109px;height:46px;background:var(--red);color:var(--white);font-size:13px}
.c-icon{width:38px;height:38px;border-radius:50%;background:var(--red);display:flex;align-items:center;justify-content:center}
.c-text{font-size:14px;line-height:22px;color:var(--white)}
.rule{left:173px;top:3533px;width:854px;height:1px;background:#8a8a8a}
.copy{left:173px;top:3576px;font-size:13px;color:var(--white)}
.social{left:920px;top:3570px;display:flex;gap:7px}
.social span{width:31px;height:31px;border-radius:50%;background:var(--white)}
</style>
</head>
<body>

<header>
  <div class="abs hero"></div>
  <div class="abs hero-photo" role="img" aria-label="Runner's legs in dark sneakers striding on misty asphalt"></div>
  <div class="abs brand-dot"></div>
  <div class="abs brand display">PaceKite</div>
  <nav class="abs nav display"><span>Home</span><span>About</span><span>Reviews</span><span>Blog</span><span>Contact Us</span></nav>
  <h1 class="abs hero-title display">PaceKite</h1>
  <p class="abs hero-sub display">Roundups on footwear<br>products</p>
  <a class="abs btn btn-light">Read More</a>
  <div class="abs arrows" style="left:173px;top:528px">
    <svg width="24" height="42" viewBox="0 0 24 42"><path d="M22 2 L3 21 L22 40" fill="none" stroke="#fff" stroke-width="2.5"/></svg>
    <svg width="24" height="42" viewBox="0 0 24 42"><path d="M2 2 L21 21 L2 40" fill="none" stroke="#fff" stroke-width="2.5"/></svg>
  </div>
</header>

<div class="abs mist" style="top:735px;height:500px"></div>
<div class="abs mist" style="top:1250px;height:500px;opacity:.8"></div>
<div class="abs mist" style="top:1950px;height:700px;opacity:.8"></div>
<div class="abs mist" style="top:2650px;height:500px;opacity:.7"></div>

<section>
  <h2 class="abs about-title h2 display">About <span class="red">PaceKite</span></h2>
  <p class="abs about-text body-text">Nemo enim ipsam voluptatem quia voluptas sit aspernatur aut odit aut fugit, sed quia consequuntur magni dolores eos qui ra tione voluptatem sequi nesciunt. Neque porro quisquam est, qui dolorem ipsum quia dolor sit amet, consectetur, adipisci velit, sed quia non numquam eius modi tempora incidunt ut labore et dolore magnam aliquam quaerat voluptatem.</p>
  <a class="abs btn btn-red">Read More</a>
  <div class="abs about-card"></div>
  <div class="abs about-img" role="img" aria-label="Hiker's legs in teal trail shoes on a rocky mountain summit"></div>
</section>

<section>
  <h2 class="abs center-title h2 display" style="top:1318px">Reviews on<br><span class="red">Footwear Products</span></h2>
  <div class="abs panel panel-right"></div>
  <div class="abs photo review-img" role="img" aria-label="Hiking boots standing on a rock above a mountain valley"></div>
  <h3 class="abs item-title display" style="left:659px;top:1518px;color:#fff">Review 1</h3>
  <p class="abs item-text" style="left:659px;top:1561px">Nemo enim ipsam voluptatem quia voluptas sit aspernatur aut odit aut fugit, sed quia consequuntur magni dolores eos qui ra tione voluptatem sequi nesciunt.</p>
  <h3 class="abs item-title display" style="left:659px;top:1668px;color:#fff">Review 2</h3>
  <p class="abs item-text" style="left:659px;top:1711px">Nemo enim ipsam voluptatem quia voluptas sit aspernatur aut odit aut fugit, sed quia consequuntur magni dolores eos qui ra tione voluptatem sequi nesciunt.</p>
  <div class="abs arrows" style="left:659px;top:1810px">
    <svg width="18" height="30" viewBox="0 0 18 30"><path d="M16 2 L3 15 L16 28" fill="none" stroke="#fff" stroke-width="2"/></svg>
    <svg width="18" height="30" viewBox="0 0 18 30"><path d="M2 2 L15 15 L2 28" fill="none" stroke="#fff" stroke-width="2"/></svg>
  </div>
</section>

<section>
  <h2 class="abs center-title h2 display" style="top:2010px">Roundups on<br><span class="red">Footwear Products</span></h2>
  <div class="abs panel panel-left"></div>
  <h3 class="abs item-title display" style="left:173px;top:2211px;color:#fff">Roundups 1</h3>
  <p class="abs item-text" style="left:173px;top:2254px">Nemo enim ipsam voluptatem quia voluptas sit aspernatur aut odit aut fugit, sed quia consequuntur magni dolores eos qui ra tione voluptatem sequi nesciunt.</p>
  <h3 class="abs item-title display" style="left:173px;top:2361px;color:#fff">Roundups 2</h3>
  <p class="abs item-text" style="left:173px;top:2404px">Nemo enim ipsam voluptatem quia voluptas sit aspernatur aut odit aut fugit, sed quia consequuntur magni dolores eos qui ra tione voluptatem sequi nesciunt.</p>
  <div class="abs arrows" style="left:173px;top:2503px">
    <svg width="18" height="30" viewBox="0 0 18 30"><path d="M16 2 L3 15 L16 28" fill="none" stroke="#fff" stroke-width="2"/></svg>
    <svg width="18" height="30" viewBox="0 0 18 30"><path d="M2 2 L15 15 L2 28" fill="none" stroke="#fff" stroke-width="2"/></svg>
  </div>
  <div class="abs photo roundup-img" role="img" aria-label="White and blue flip-flops resting on driftwood at the beach"></div>
</section>

<section>
  <h2 class="abs center-title h2 display" style="top:2694px">Our<br><span class="red">Footwear Products</span></h2>
  <svg class="abs" style="left:50px;top:2922px" width="22" height="50" viewBox="0 0 22 50"><path d="M20 2 L3 25 L20 48" fill="none" stroke="#222" stroke-width="1.5"/></svg>
  <svg class="abs" style="left:1128px;top:2922px" width="22" height="50" viewBox="0 0 22 50"><path d="M2 2 L19 25 L2 48" fill="none" stroke="#222" stroke-width="1.5"/></svg>
  <div class="abs product" style="left:122px"><div class="abs product-shoe" role="img" aria-label="Pair of black sneakers with white soles"></div></div>
  <div class="abs product" style="left:370px"><div class="abs product-shoe" role="img" aria-label="Black sneakers shown from above and side"></div></div>
  <div class="abs product" style="left:617px"><div class="abs product-shoe" role="img" aria-label="Black sneakers shown at an angle"></div></div>
  <div class="abs product" style="left:865px"><div class="abs product-shoe" role="img" aria-label="Single black sneaker in side view"></div></div>
</section>

<footer>
  <div class="abs footer"></div>
  <div class="abs foot-dot"></div>
  <div class="abs foot-brand display">PaceKite</div>
  <h4 class="abs foot-h display" style="left:478px;top:3256px">Subscribe to our<br>newsletter</h4>
  <div class="abs email">Email</div>
  <a class="abs btn subscribe">Subscribe</a>
  <h4 class="abs foot-h display" style="left:815px;top:3256px">Contact Us</h4>
  <div class="abs c-icon" style="left:815px;top:3302px">
    <svg width="18" height="18" viewBox="0 0 24 24"><path d="M6.6 10.8a15.1 15.1 0 0 0 6.6 6.6l2.2-2.2a1 1 0 0 1 1-.25 11.4 11.4 0 0 0 3.6.57 1 1 0 0 1 1 1V20a1 1 0 0 1-1 1A17 17 0 0 1 3 4a1 1 0 0 1 1-1h3.5a1 1 0 0 1 1 1c0 1.25.2 2.45.57 3.57a1 1 0 0 1-.25 1z" fill="none" stroke="#fff" stroke-width="1.6"/></svg>
  </div>
  <p class="abs c-text" style="left:867px;top:3310px">TEL: + 555 014 2288</p>
  <div class="abs c-icon" style="left:815px;top:3358px">
    <svg width="18" height="18" viewBox="0 0 24 24"><path d="M12 22s7-7.2 7-12.5a7 7 0 0 0-14 0C5 14.8 12 22 12 22z" fill="none" stroke="#fff" stroke-width="1.6"/><circle cx="12" cy="9.5" r="2.5" fill="none" stroke="#fff" stroke-width="1.6"/></svg>
  </div>
  <p class="abs c-text" style="left:867px;top:3357px">ADDRESS:<br>Level 14 Harbor Row,<br>North Vale, 4810<br>Westland</p>
  <div class="abs rule"></div>
  <p class="abs copy">Copyrights @ 2021 PaceKite. All Rights Reserved.</p>
  <div class="abs social" aria-label="Social links"><span></span><span></span><span></span></div>
</footer>

</body>
</html>
```